Companybrochure for Consulting & Financing Firm

I need to have a Company Brochure asap for our company. We have a website that describes what we do, but we need also a brochure, that can be sent by PDF of eventually be printed as well.

The brochure should be short but nice and appealing to the customers.

We provide professional management consulting and help our customers to get finance for very diferent projects. Our business has a lot to do with personal relations, but also we are very professional in the way we work and how develop the solutions for our clients. Our clients are mainly government-owned firm, but also private trading companies and wealthy private investors.

Our customers are mainly in Latin America, but the company is headquater is in Switzerland. We are opening offices in Panama and Caracas, this should be easaly be adabtable later.

Please have a look at our website www.vorelpartners.ch. In the brochure, we would segment our services in 1.) Project Developments 2.) Management Conulting 3.) Investment Management and 4.) Finance Solutions.

Also do have a look at www.vorelpartners.ch
(Click E for the English version)
Updates

I managed to put the Mock-Up to the Website.
It is actually not really a mock-up, it is a version I have designed myself.
Well as I am not a designer, I hope you can make it much better.
The content however is what I would put in any other design as well.

Target Market(s)

Top Management, Investors, Entrepreneurs, Government Officials

Industry/Entity Type

Management Consulting

Requirements
Must have
• Design should reflect this image elements:

We are entrepreneurs.
We are comitted to get things done.
We work closely with the client side by side.
We are a professional partner.
We are not afraid of delivering unconventional solutions.
We look at the problem from various angles.
We analyse, develop solutions and implent results.
Should not have
• Typical US-American style elements. We do not want to give the impression of being a US company.

We do not want to appear to be neo-liberal. We are a politically neutral professional consulting firm.

```html
<!DOCTYPE html>
<html lang="en">
<head>
<meta charset="utf-8">
<title>Vorel Partners AG – Brochure Spread</title>
<link rel="stylesheet" href="https://fonts.googleapis.com/css2?family=Arimo:wght@400;700&family=Open+Sans:wght@600;700&display=swap">
<style>
  :root {
    --canvas: #c4c5c7;
    --paper: #ffffff;
    --panel-grey: #d3d4d6;
    --band-dark: #2c4680;
    --band-light: #3f72b8;
    --navy-text: #2e3a6b;
    --heading: #2f3d66;
    --heading-band: #e7e8ea;
    --divider: #3b4a6b;
    --body-grey: #6e6f72;
    --ink: #1e1e1e;
  }
  * { margin: 0; padding: 0; box-sizing: border-box; }
  html, body { width: 1200px; height: 434px; overflow: hidden; }
  body { background: var(--canvas); position: relative; font-family: "Arimo", Arial, sans-serif; }

  .page { position: absolute; top: 12px; height: 409px; overflow: hidden; background: var(--panel-grey); }
  .page--cover { left: 17px; width: 578px; }
  .page--service { left: 605px; width: 579px; }

  /* Cover */
  .cover-top { position: absolute; left: 0; top: 0; width: 100%; height: 224px; background: var(--paper); }
  .brand-name {
    position: absolute; right: 48px; top: 30px;
    font-family: "Arimo", Arial, sans-serif; font-weight: 700; font-size: 23px;
    color: var(--ink); letter-spacing: -0.2px;
  }
  .tagline-band {
    position: absolute; left: 0; top: 224px; width: 100%; height: 57px;
    background: linear-gradient(90deg, var(--band-dark) 0%, var(--band-light) 55%, var(--band-dark) 100%);
  }
  .tagline {
    position: absolute; left: 51px; top: 14px;
    font-weight: 700; font-size: 23px; color: #fff; letter-spacing: 0.1px;
  }
  .intro {
    position: absolute; left: 51px; top: 299px;
    font-family: "Open Sans", Arial, sans-serif; font-weight: 700; font-size: 11px;
    line-height: 15.2px; color: var(--navy-text);
  }
  .intro ul { list-style: none; }

  /* Service page */
  .photo {
    position: absolute; left: 0; top: 0; width: 100%; height: 210px;
    background: radial-gradient(ellipse at 55% 35%, #9fd26a 0%, #5faa3c 35%, #2f7a2a 70%, #1f5a22 100%);
  }
  .divider-band { position: absolute; left: 0; top: 210px; width: 100%; height: 14px; background: var(--divider); }
  .heading-band { position: absolute; left: 0; top: 224px; width: 100%; height: 40px; background: var(--heading-band); }
  .service-title {
    position: absolute; left: 51px; top: 3px;
    font-weight: 700; font-size: 25px; color: var(--heading);
  }
  .service-copy {
    position: absolute; left: 51px; top: 273px; width: 470px;
    font-size: 10px; line-height: 12.5px; color: var(--body-grey);
  }
  .service-copy p + p { margin-top: 12.5px; }
</style>
</head>
<body>
  <section class="page page--cover">
    <div class="cover-top">
      <div class="brand-name">Vorel Partners AG</div>
    </div>
    <div class="tagline-band">
      <h1 class="tagline">&gt; Analyze &gt;&gt; Develop &gt;&gt;&gt; Deliver</h1>
    </div>
    <div class="intro">
      <p>We are a professional consulting, financing and<br>investment firm operating in the fields of:</p>
      <ul>
        <li>&gt; Project Development</li>
        <li>&gt; Management Consulting</li>
        <li>&gt; Investment Management</li>
        <li>&gt; Finance Solutions</li>
      </ul>
    </div>
  </section>

  <section class="page page--service">
    <div class="photo" role="img" aria-label="Photo of a hand holding soil with a young green plant sprouting, on a green background"></div>
    <div class="divider-band"></div>
    <div class="heading-band">
      <h2 class="service-title">&gt;&gt; Project Development</h2>
    </div>
    <div class="service-copy">
      <p>Sometimes a project with high potential has to be developed before its economic value becomes apparent.</p>
      <p>In such situations, we participate financially in the project and commit ourselves as entrepreneurs together with the owners.</p>
      <p>We also take care of project management.</p>
    </div>
  </section>
</body>
</html>
```